Business Card Design

Company is a Commercial Building Company specialising in New Construction and existing refurbishments

Industry/Entity Type

Business

Contact Information for Business Card

Liam Porter
Construction Manager
E Liam@marshbuilding.com.au
M 0400 213 594
Mail 14 Tarrant Rise Harbourton WA 6342

```html
<!DOCTYPE html>
<html lang="en">
<head>
<meta charset="utf-8">
<title>Marsh Building &amp; Construction – Business Card</title>
<link rel="stylesheet" href="https://fonts.googleapis.com/css2?family=Roboto+Condensed:wght@500&family=Source+Sans+3:wght@400;600;700&display=swap">
<style>
  :root {
    --backdrop: #4b4c4e;
    --navy: #353b4e;
    --paper: #ffffff;
    --cyan: #12b5d4;
    --orange: #f48a1f;
    --ink: #2f3444;
    --white: #ffffff;
  }
  * { margin: 0; padding: 0; box-sizing: border-box; }
  html, body {
    width: 1200px;
    height: 1000px;
    overflow: hidden;
    background: var(--backdrop);
  }
  .canvas {
    position: relative;
    width: 1200px;
    height: 1000px;
  }
  .card {
    position: absolute;
    width: 560px;
    height: 346px;
    overflow: hidden;
  }
  .card--front {
    left: 210px;
    top: 150px;
    background: var(--navy);
  }
  .card--back {
    left: 390px;
    top: 515px;
    background: var(--paper);
  }

  .wordmark {
    position: absolute;
    font-family: "Roboto Condensed", "Arial Narrow", sans-serif;
    font-weight: 500;
    text-align: center;
    line-height: 1.05;
  }
  .wordmark__main { display: block; font-size: 31px; }
  .wordmark__sub { display: block; font-size: 26px; }

  .card--front .wordmark {
    left: 0;
    width: 560px;
    top: 216px;
    color: var(--white);
  }
  .card--back .wordmark {
    left: 40px;
    width: 230px;
    top: 204px;
    color: var(--ink);
  }
  .card--back .wordmark__main { font-size: 24px; }
  .card--back .wordmark__sub { font-size: 20px; }

  .contact {
    position: absolute;
    left: 312px;
    top: 52px;
    font-family: "Source Sans 3", "Helvetica Neue", sans-serif;
    color: var(--ink);
  }
  .contact__name {
    font-size: 21px;
    font-weight: 700;
    color: var(--cyan);
    line-height: 1.1;
  }
  .contact__role {
    font-size: 15px;
    margin-top: 3px;
  }
  .contact__lines {
    list-style: none;
    margin-top: 34px;
    font-size: 15px;
  }
  .contact__lines li {
    display: flex;
    align-items: center;
    gap: 6px;
    height: 25px;
  }
  .contact__lines svg { flex: none; }
  .contact__office {
    margin-top: 32px;
    margin-left: 3px;
    font-size: 15px;
    line-height: 19px;
    font-style: normal;
  }
  .contact__company {
    font-weight: 600;
    color: var(--cyan);
  }

  .stripe {
    position: absolute;
    bottom: 0;
    height: 15px;
  }
  .stripe--cyan { left: 0; width: 291px; background: var(--cyan); }
  .stripe--orange { left: 298px; width: 262px; background: var(--orange); }
</style>
</head>
<body>
<main class="canvas">

  <section class="card card--front" aria-label="Business card front">
    <p class="wordmark">
      <span class="wordmark__main">MARSH BUILDING</span>
      <span class="wordmark__sub">&amp; CONSTRUCTION</span>
    </p>
  </section>

  <section class="card card--back" aria-label="Business card back">
    <p class="wordmark">
      <span class="wordmark__main">MARSH BUILDING</span>
      <span class="wordmark__sub">&amp; CONSTRUCTION</span>
    </p>

    <div class="contact">
      <h1 class="contact__name">Liam Porter</h1>
      <p class="contact__role">Construction Manager</p>

      <ul class="contact__lines">
        <li>
          <svg width="14" height="18" viewBox="0 0 14 18" aria-hidden="true">
            <rect x="2" y="1" width="10" height="16" rx="2" fill="none" stroke="var(--orange)" stroke-width="1.6"/>
            <line x1="5.5" y1="14" x2="8.5" y2="14" stroke="var(--orange)" stroke-width="1.4"/>
          </svg>
          <span>Liam@marshbuilding.com.au</span>
        </li>
        <li>
          <svg width="16" height="12" viewBox="0 0 16 12" aria-hidden="true">
            <rect x="0" y="0" width="16" height="12" fill="var(--orange)"/>
            <polyline points="0.5,0.5 8,7 15.5,0.5" fill="none" stroke="var(--white)" stroke-width="1.3"/>
          </svg>
          <span>0400 213 594</span>
        </li>
      </ul>

      <address class="contact__office">
        <span class="contact__company">Marsh Building &amp; Construction</span><br>
        14 Tarrant Rise<br>
        Harbourton WA 6342
      </address>
    </div>

    <div class="stripe stripe--cyan"></div>
    <div class="stripe stripe--orange"></div>
  </section>

</main>
</body>
</html>
```